Upmarket Dessert Lounge needs a Business Card Design

We are an upmarket dessert lounge needing a business card to match our image.

We want something that is simple yet beautiful, feminine, classy, sophisticated and elegant. We want it to stand out and don't mind if it is bold.

The design should include our logo and colours of red or maroon with gold highlights. We don't mind if black is used.

Marlow & Quince

Target Market(s)

For those who like to indulge or treat themselves and give in to their temptations on good quality desserts.

Industry/Entity Type

Business

Requirements
Must have
• Must include our logo and our name

Marlow & Quince

M & Q

```html
<!DOCTYPE html>
<html lang="en">
<head>
<meta charset="utf-8">
<title>Marlow &amp; Quince — Business Card</title>
<link href="https://fonts.googleapis.com/css2?family=Cinzel:wght@400;500&family=Open+Sans:wght@400&family=Tinos:wght@400;700&display=swap" rel="stylesheet">
<style>
  :root {
    --maroon: #7a1416;
    --cream: #f6cf97;
    --ink: #3a3a3a;
    --rule: #b9b9b9;
    --paper: #ffffff;
    --backdrop: #ece6df;
  }
  html, body {
    margin: 0;
    padding: 0;
    width: 1200px;
    height: 402px;
    overflow: hidden;
    background: var(--backdrop);
  }
  .canvas {
    position: relative;
    width: 1200px;
    height: 402px;
  }
  .card {
    position: absolute;
    top: 55px;
    width: 512px;
    height: 291px;
    border-radius: 18px;
    overflow: hidden;
    box-shadow: 0 2px 8px rgba(0,0,0,0.18);
  }
  .card--front { left: 59px; background: var(--paper); }
  .card--back { left: 633px; background: var(--maroon); }

  .brand-name {
    position: absolute;
    left: 0;
    right: 0;
    top: 78px;
    text-align: center;
    font-family: "Cinzel", serif;
    font-weight: 400;
    font-size: 30px;
    letter-spacing: 1px;
    color: var(--maroon);
  }

  .contact-row {
    position: absolute;
    top: 187px;
    left: 0;
    right: 0;
    height: 36px;
    font-family: "Open Sans", sans-serif;
    font-size: 13px;
    line-height: 17px;
    color: var(--ink);
  }
  .contact-address {
    position: absolute;
    right: 344px;
    top: 0;
    text-align: right;
  }
  .contact-divider {
    position: absolute;
    top: 0;
    width: 1px;
    height: 36px;
    background: var(--rule);
  }
  .contact-divider--first { left: 176px; }
  .contact-divider--second { left: 300px; }
  .contact-list {
    position: absolute;
    top: 0;
    margin: 0;
    padding: 0;
    list-style: none;
  }
  .contact-list--phones { left: 183px; }
  .contact-list--online { left: 309px; }
  .contact-list li {
    display: flex;
    align-items: center;
    gap: 5px;
    height: 17px;
  }
  .contact-icon {
    width: 10px;
    height: 10px;
    fill: var(--maroon);
    flex: none;
  }

  .accent-band {
    position: absolute;
    left: 0;
    right: 0;
    top: 238px;
    height: 17px;
    background: var(--maroon);
  }
  .accent-band__highlight {
    position: absolute;
    left: 326px;
    top: -1px;
    width: 106px;
    height: 15px;
    border: 2px solid var(--paper);
    border-radius: 10px;
    background: var(--cream);
  }

  .holder {
    position: absolute;
    left: 0;
    right: 0;
    top: 273px;
    text-align: center;
    font-family: "Tinos", serif;
    color: var(--maroon);
    line-height: 1;
    margin-top: -4px;
  }
  .holder__name { font-weight: 700; font-size: 17px; letter-spacing: 0.5px; }
  .holder__title { font-weight: 400; font-size: 13px; }

  .monogram {
    position: absolute;
    left: 0;
    right: 0;
    top: 105px;
    text-align: center;
    font-family: "Cinzel", serif;
    font-weight: 400;
    font-size: 68px;
    line-height: 1;
    color: var(--cream);
  }
</style>
</head>
<body>
<main class="canvas">
  <section class="card card--front" aria-label="Card front">
    <div class="brand-name">Marlow &amp; Quince</div>

    <div class="contact-row">
      <div class="contact-address">00, Complex name<br>City, State 000 000</div>
      <span class="contact-divider contact-divider--first"></span>
      <ul class="contact-list contact-list--phones">
        <li>
          <svg class="contact-icon" viewBox="0 0 10 10" aria-hidden="true"><path d="M2 0.5 L3.6 2.6 L2.7 3.6 Q3.7 5.8 6.4 7.3 L7.4 6.4 L9.5 8 L8.3 9.5 Q4.5 9.5 2 6.5 Q0.3 4.2 0.5 1.7 Z"/></svg>
          555-014-2260
        </li>
        <li>
          <svg class="contact-icon" viewBox="0 0 10 10" aria-hidden="true"><path d="M2.5 0 H7.5 V10 H2.5 Z M3.3 1.2 V6.8 H6.7 V1.2 Z"/></svg>
          555-014-2260
        </li>
      </ul>
      <span class="contact-divider contact-divider--second"></span>
      <ul class="contact-list contact-list--online">
        <li>
          <svg class="contact-icon" viewBox="0 0 10 10" aria-hidden="true"><path d="M0 2 H10 V8.5 H0 Z"/><path d="M0 2 L5 5.6 L10 2" fill="none" stroke="#fff" stroke-width="0.9"/></svg>
          info@marlowquince.com
        </li>
        <li>
          <svg class="contact-icon" viewBox="0 0 10 10" aria-hidden="true"><circle cx="5" cy="5" r="4.5"/><path d="M0.5 5 H9.5 M5 0.5 V9.5 M5 0.5 Q2.5 5 5 9.5 M5 0.5 Q7.5 5 5 9.5" fill="none" stroke="#fff" stroke-width="0.7"/></svg>
          www.marlowquince.com
        </li>
      </ul>
    </div>

    <div class="accent-band"><span class="accent-band__highlight"></span></div>

    <div class="holder"><span class="holder__name">YOUR NAME /</span> <span class="holder__title">Title</span></div>
  </section>

  <section class="card card--back" aria-label="Card back">
    <div class="monogram">M &amp; Q</div>
  </section>
</main>
</body>
</html>
```